Corvel Capital LLC

Need Professional Business cards for New Investment Fund

Target Market(s)

High Quality investors

Industry/Entity Type

Financial

Contact Information for Business Card

Phone Number +1 555 284 6190
Name Lukas Varenko
Title Fund Manager
email lv@FundCorvel.com
Website www.FundCorvel.com

Colors

Designer to choose colors to be used in the design.

Requirements
Must have
• Must have our Logo and all of the above. Must be made so lettering and loge can be raised

```html
<!DOCTYPE html>
<html lang="en">
<head>
<meta charset="utf-8">
<title>Quellmar Capital — Business Card</title>
<link rel="stylesheet" href="https://fonts.googleapis.com/css2?family=Jost:wght@400;600&display=swap">
<style>
  :root {
    --backdrop: #9a9a9a;
    --paper: #f7f7f5;
    --forest: #2f3b2d;
    --leaf: #3fae3a;
    --edge: #2e9a22;
    --ink: #6d6d6d;
    --white: #ffffff;
  }
  * { box-sizing: border-box; margin: 0; padding: 0; }
  html, body {
    width: 1200px; height: 943px; overflow: hidden;
    background: var(--backdrop);
    font-family: "Jost", sans-serif;
  }
  .sheet {
    position: relative; width: 1200px; height: 943px;
    display: flex; flex-direction: column; align-items: center;
    justify-content: center; gap: 43px;
  }
  .card {
    position: relative; width: 700px; height: 400px;
    border-bottom: 5px solid var(--edge);
    overflow: hidden;
  }
  .card--front { background: var(--paper); }
  .card--back { background: var(--forest); display: flex; align-items: center; justify-content: center; }

  .brand {
    position: absolute; left: 56px; top: 48px;
    display: flex; align-items: center; gap: 10px;
    color: var(--leaf); font-weight: 600; font-size: 26px; letter-spacing: 0.06em;
  }
  .brand__dot { width: 14px; height: 14px; border-radius: 50%; background: var(--leaf); }

  .watermark {
    position: absolute; right: 28px; bottom: 36px;
    font-size: 56px; font-weight: 600; letter-spacing: 0.04em;
    color: var(--leaf); opacity: 0.07;
  }
  .watermark--back {
    left: 28px; right: auto; top: 30px; bottom: auto;
    color: var(--white); opacity: 0.08;
  }

  .person { position: absolute; left: 56px; top: 190px; }
  .person__name {
    color: var(--leaf); font-weight: 600; font-size: 26px;
    letter-spacing: 0.08em; text-transform: uppercase;
  }
  .person__title { color: var(--ink); font-size: 19px; letter-spacing: 0.05em; margin-top: 2px; }

  .contacts { position: absolute; left: 56px; top: 282px; list-style: none; }
  .contacts li {
    display: flex; align-items: center; gap: 12px;
    color: var(--ink); font-size: 18px; letter-spacing: 0.05em; line-height: 30px;
  }
  .contacts svg { width: 16px; height: 16px; flex: none; }

  .brand--back {
    position: static; color: var(--white); font-size: 52px; gap: 16px;
  }
  .brand--back .brand__dot { width: 24px; height: 24px; background: var(--leaf); }
</style>
</head>
<body>
<main class="sheet">
  <section class="card card--front" aria-label="Card front">
    <div class="brand"><span class="brand__dot"></span>QUELLMAR</div>
    <div class="watermark" aria-hidden="true">QUELLMAR</div>
    <div class="person">
      <h1 class="person__name">Lukas Varenko</h1>
      <p class="person__title">Fund Manager</p>
    </div>
    <ul class="contacts">
      <li>
        <svg viewBox="0 0 16 16" aria-hidden="true"><path d="M4 1.5l2.5 3-1.6 1.6a9 9 0 0 0 5 5l1.6-1.6 3 2.5-1.5 2.5C7 14 2 9 1.5 3z" fill="var(--leaf)"/></svg>
        +1 555 284 6190
      </li>
      <li>
        <svg viewBox="0 0 16 16" aria-hidden="true"><rect x="1.5" y="3.5" width="13" height="9" fill="none" stroke="var(--leaf)" stroke-width="1.4"/><path d="M1.5 3.5l6.5 5 6.5-5" fill="none" stroke="var(--leaf)" stroke-width="1.4"/></svg>
        lv@FundCorvel.com
      </li>
      <li>
        <svg viewBox="0 0 16 16" aria-hidden="true"><circle cx="8" cy="8" r="6.5" fill="none" stroke="var(--leaf)" stroke-width="1.4"/><ellipse cx="8" cy="8" rx="3" ry="6.5" fill="none" stroke="var(--leaf)" stroke-width="1.2"/><path d="M1.5 8h13" stroke="var(--leaf)" stroke-width="1.2"/></svg>
        www.FundCorvel.com
      </li>
    </ul>
  </section>

  <section class="card card--back" aria-label="Card back">
    <div class="watermark watermark--back" aria-hidden="true">QUELLMAR</div>
    <div class="brand brand--back"><span class="brand__dot"></span>QUELLMAR</div>
  </section>
</main>
</body>
</html>
```